Finiding oppertunites in Real Estate 6.15.20

size of ad 7” x 9.6”
1-I like the ad to stand out and attract people's attention.
2-you should be able to see the text of the ad clearly .. see the attachment anything in yellow is instructions.
3-the list of topics should not be the main part of the ad
4-if you decide you want a picture or vector of a person .. (you decide)
then it should be a white male about 25-30 years old wearing a solid white or blue shirt and not long hair.
5-leave 1 inch for footer
see attachment
Good luck

Target Market(s)

potential male students 25-35 years of age

Industry/Entity Type

Education

Requirements
Must have
• will stand out and people would want to see it.
should be able to read the words of ad
Nice to have
• how to make money in real estate on one line

```html
<!DOCTYPE html>
<html lang="en">
<head>
<meta charset="utf-8">
<title>Real Estate Career Course</title>
<link href="https://fonts.googleapis.com/css2?family=Montserrat:wght@400;500;600;700;800;900&display=swap" rel="stylesheet">
<style>
  :root {
    --navy: #1c2f5a;
    --teal: #2bb3c0;
    --teal-deep: #1a8fa0;
    --teal-soft: #cdeff2;
    --ink: #2a3348;
    --paper: #ffffff;
  }
  * { margin: 0; padding: 0; box-sizing: border-box; }
  html, body { width: 853px; height: 1200px; overflow: hidden; background: #e9edf1; }
  body { font-family: "Montserrat", Arial, sans-serif; color: var(--ink); }

  .poster {
    position: relative; width: 853px; height: 1200px; overflow: hidden;
    background: linear-gradient(180deg, #ffffff 0%, #f3fbfc 55%, #e6f6f8 100%);
  }
  .wash { position: absolute; inset: 0; width: 853px; height: 1200px; }

  .headline { position: absolute; left: 62px; top: 58px; line-height: 1; }
  .headline .line-1 { display: block; font-size: 46px; font-weight: 900; color: var(--teal-deep); letter-spacing: .5px; }
  .headline .line-2 { display: block; font-size: 46px; font-weight: 900; color: var(--navy); letter-spacing: .5px; margin-top: 4px; }

  .intro { position: absolute; left: 62px; top: 178px; list-style: none; width: 560px; }
  .intro li { display: flex; align-items: flex-start; gap: 12px; font-size: 16px; font-weight: 600; color: var(--navy); line-height: 1.3; margin-bottom: 12px; }
  .intro svg { flex: none; margin-top: 1px; }

  .hero-art {
    position: absolute; left: 215px; top: 300px; width: 560px; height: 300px;
    border-radius: 150px 40px 150px 40px;
    background: radial-gradient(ellipse at 55% 60%, #ffffff 0%, #d6f1f4 45%, #8fd6de 100%);
  }

  .badge {
    position: absolute; left: 105px; top: 330px; width: 140px; height: 140px; border-radius: 50%;
    background: var(--navy); border: 6px solid var(--teal);
    display: flex; align-items: center; justify-content: center; text-align: center;
    color: var(--paper); font-size: 17px; font-weight: 800; line-height: 1.15; text-transform: uppercase;
  }

  .sessions { position: absolute; left: 62px; top: 622px; display: flex; align-items: center; gap: 14px; }
  .sessions .count { font-size: 150px; font-weight: 900; color: var(--navy); line-height: .8; letter-spacing: -6px; }
  .sessions .words { line-height: 1; }
  .sessions .session-label { display: block; font-size: 48px; font-weight: 900; color: var(--teal-deep); }
  .sessions .start-date { display: block; font-size: 33px; font-weight: 800; color: var(--navy); margin-top: 8px; }

  .topics-banner {
    position: absolute; left: 62px; top: 790px; width: 729px; height: 40px;
    background: var(--navy); color: var(--paper);
    display: flex; align-items: center; justify-content: center;
    font-size: 18px; font-weight: 800; letter-spacing: 3px;
  }
  .topics { position: absolute; left: 80px; top: 852px; width: 710px; display: flex; justify-content: space-between; }
  .topics ul { list-style: none; width: 220px; }
  .topics li { display: flex; align-items: center; gap: 10px; font-size: 15px; font-weight: 600; color: var(--ink); margin-bottom: 13px; }
  .topics li::before { content: ""; width: 9px; height: 9px; border-radius: 50%; background: var(--teal); flex: none; }

  .footer { position: absolute; left: 0; bottom: 0; width: 853px; height: 125px; }
  .footer .rule { position: absolute; left: 62px; right: 62px; top: 0; height: 3px; background: var(--teal); }
  .footer .contact {
    position: absolute; left: 0; right: 0; top: 38px; text-align: center;
    font-size: 17px; font-weight: 700; color: var(--navy);
  }
  .footer .contact span { color: var(--teal-deep); margin: 0 10px; }
  .footer .band { position: absolute; left: 0; right: 0; bottom: 0; height: 34px; background: linear-gradient(90deg, var(--teal-deep), var(--teal)); }
</style>
</head>
<body>
<main class="poster">
  <svg class="wash" viewBox="0 0 853 1200" aria-hidden="true">
    <path d="M853 0 H600 C650 90 700 150 853 170 Z" fill="#2bb3c0" opacity=".85"/>
    <path d="M853 0 H700 C740 60 790 90 853 95 Z" fill="#1c2f5a" opacity=".9"/>
    <path d="M0 760 C80 740 120 700 150 640 L0 600 Z" fill="#cdeff2" opacity=".7"/>
    <path d="M853 620 C790 660 760 720 770 790 L853 790 Z" fill="#cdeff2" opacity=".8"/>
  </svg>

  <h1 class="headline">
    <span class="line-1">REAL ESTATE</span>
    <span class="line-2">CAREER COURSE</span>
  </h1>

  <ul class="intro">
    <li><svg width="18" height="18" viewBox="0 0 18 18"><circle cx="9" cy="9" r="9" fill="#2bb3c0"/><path d="M5 9.3l2.6 2.6L13 6.5" stroke="#fff" stroke-width="2" fill="none"/></svg>How to Make Money in Real Estate</li>
    <li><svg width="18" height="18" viewBox="0 0 18 18"><circle cx="9" cy="9" r="9" fill="#2bb3c0"/><path d="M5 9.3l2.6 2.6L13 6.5" stroke="#fff" stroke-width="2" fill="none"/></svg>For those who have wanted to work full time to get into Real Estate</li>
    <li><svg width="18" height="18" viewBox="0 0 18 18"><circle cx="9" cy="9" r="9" fill="#2bb3c0"/><path d="M5 9.3l2.6 2.6L13 6.5" stroke="#fff" stroke-width="2" fill="none"/></svg>An investment in knowledge opens up untold opportunities</li>
  </ul>

  <div class="hero-art" role="img" aria-label="Illustration of a young man in a blue suit standing beside a house on a teal background"></div>

  <div class="badge">Expert<br>Instructors</div>

  <div class="sessions">
    <span class="count">12</span>
    <span class="words">
      <span class="session-label">SESSION COURSE</span>
      <span class="start-date">CLASSES STARTING JUNE 16</span>
    </span>
  </div>

  <div class="topics-banner">A PARTIAL LISTING OF TOPICS</div>

  <div class="topics">
    <ul>
      <li>Single Family</li>
      <li>Multifamily</li>
      <li>Management</li>
      <li>Real Estate Basics</li>
      <li>Self-Employment</li>
    </ul>
    <ul>
      <li>Real Estate Law</li>
      <li>Investment Properties</li>
      <li>Foreclosures</li>
      <li>Tax Liens</li>
      <li>Due Diligence</li>
    </ul>
    <ul>
      <li>Commercial</li>
      <li>Apartments</li>
      <li>Seller Financing</li>
      <li>Flipping Homes</li>
      <li>Wholesaling</li>
    </ul>
  </div>

  <footer class="footer">
    <div class="rule"></div>
    <p class="contact">(555) 204-3187<span>|</span>hello@keystonerealtyacademy.com<span>|</span>www.keystonerealtyacademy.com</p>
    <div class="band"></div>
  </footer>
</main>
</body>
</html>
```